Business Card For Halvenmoor Financial Consulting

Hi, I would like a business card designed. Bold, modern.
Please use the same design as the logo. I have also attached the website design to see the overall theme.
Wordmark Font
Color: Hex: #01AEF7

```html
<!DOCTYPE html>
<html lang="en">
<head>
<meta charset="UTF-8">
<title>Halvenmoor Financial Consulting — Business Card</title>
<link rel="stylesheet" href="https://fonts.googleapis.com/css2?family=Poppins:ital,wght@0,400;0,600;0,700;1,400&display=swap">
<style>
  :root {
    --brand-blue: #01AEF7;
    --card-navy: #16202b;
    --card-navy-deep: #111a23;
    --pattern-steel: #2c4257;
    --text-light: #eef3f7;
    --page-bg: #1c1c1e;
  }
  * { margin: 0; padding: 0; box-sizing: border-box; }
  html, body {
    width: 1200px; height: 900px; overflow: hidden;
    background: var(--page-bg);
    font-family: "Poppins", sans-serif;
  }
  .stage {
    width: 1200px; height: 900px;
    display: flex; flex-direction: column;
    align-items: center; justify-content: center; gap: 50px;
  }
  .card {
    width: 630px; height: 360px;
    position: relative; overflow: hidden;
    background: var(--card-navy);
    box-shadow: 0 14px 30px rgba(0,0,0,0.5);
  }
  /* Front */
  .card-front__pattern {
    position: absolute; inset: 0;
    background: linear-gradient(135deg, var(--card-navy-deep) 0%, var(--pattern-steel) 50%, var(--card-navy-deep) 100%);
    opacity: 0.55;
  }
  .wordmark {
    display: flex; align-items: center; gap: 14px;
  }
  .wordmark__square {
    width: 34px; height: 34px; background: var(--brand-blue); flex: none;
  }
  .wordmark__name {
    font-weight: 700; color: var(--text-light);
    text-transform: uppercase; letter-spacing: 0.06em; line-height: 1.15;
  }
  .card-front .wordmark {
    position: absolute; left: 50%; top: 50%;
    transform: translate(-50%, -50%);
    background: var(--card-navy); padding: 18px 26px;
  }
  .card-front .wordmark__name { font-size: 26px; }
  /* Back */
  .card-back .wordmark { position: absolute; left: 40px; top: 36px; z-index: 2; }
  .card-back .wordmark__square { width: 26px; height: 26px; }
  .card-back .wordmark__name { font-size: 19px; }
  .contact {
    position: absolute; left: 40px; top: 128px; z-index: 2;
    color: var(--text-light); font-size: 14px; line-height: 1.55;
    white-space: nowrap;
  }
  .contact__address { margin-bottom: 14px; }
  .contact__row { display: flex; align-items: center; gap: 10px; }
  .contact__icon { width: 13px; height: 13px; flex: none; }
  .person {
    position: absolute; right: 40px; top: 150px; text-align: right; z-index: 2;
  }
  .person__name {
    color: var(--brand-blue); font-weight: 700; font-size: 20px;
    letter-spacing: 0.02em; text-transform: uppercase;
  }
  .person__title { color: var(--text-light); font-style: italic; font-size: 15px; }
  .accent-bar {
    position: absolute; right: 0; top: 154px;
    width: 12px; height: 46px; background: var(--brand-blue);
  }
  .corner-panel {
    position: absolute; right: 70px; bottom: 0;
    width: 190px; height: 130px;
    background: linear-gradient(160deg, var(--card-navy-deep) 0%, var(--card-navy-deep) 55%, #5c7c98 100%);
    box-shadow: -6px -6px 18px rgba(0,0,0,0.45);
    z-index: 1;
  }
</style>
</head>
<body>
<main class="stage">
  <section class="card card-front" aria-label="Card front">
    <div class="card-front__pattern" role="img" aria-label="Tiled pattern of the brand symbol"></div>
    <div class="wordmark">
      <span class="wordmark__square"></span>
      <span class="wordmark__name">Halvenmoor<br>Financial Consulting</span>
    </div>
  </section>

  <section class="card card-back" aria-label="Card back">
    <div class="wordmark">
      <span class="wordmark__square"></span>
      <span class="wordmark__name">Halvenmoor<br>Financial Consulting</span>
    </div>

    <div class="contact">
      <p class="contact__address">3417 Larkhaven Road<br>Westmere CA 90412</p>
      <p class="contact__row">
        <svg class="contact__icon" viewBox="0 0 16 16"><path fill="#01AEF7" d="M3 1l3 3-2 2c1 2 3 4 6 6l2-2 3 3-2 2C7 15 1 9 1 3z"/></svg>
        555-014-2280
      </p>
      <p class="contact__row">
        <svg class="contact__icon" viewBox="0 0 16 16"><rect x="1" y="3" width="14" height="10" fill="#01AEF7"/><path d="M1 3l7 6 7-6" fill="none" stroke="#16202b" stroke-width="1.5"/></svg>
        info@HalvenmoorConsulting.com
      </p>
      <p class="contact__row">
        <svg class="contact__icon" viewBox="0 0 16 16"><circle cx="8" cy="8" r="6.5" fill="none" stroke="#01AEF7" stroke-width="1.6"/><path d="M1.5 8h13M8 1.5c-3 3.5-3 9.5 0 13M8 1.5c3 3.5 3 9.5 0 13" fill="none" stroke="#01AEF7" stroke-width="1.2"/></svg>
        www.HalvenmoorConsulting.com
      </p>
    </div>

    <div class="person">
      <p class="person__name">Marek Solvane</p>
      <p class="person__title">President</p>
    </div>
    <span class="accent-bar"></span>

    <div class="corner-panel" role="img" aria-label="Raised panel with a partial brand symbol"></div>
  </section>
</main>
</body>
</html>
```